Classy, Elegant, Simple Business Card Design

Looking to have a classy, simple, and elegant design. Want a top notch designed business card. I really like the look of the new torvane credit card. I also like the design I attached. I am trying to reach 21-29 year old females for booking us for there wedding or event. We offer Disc Jockey Service, Photo Booth Rentals, and Uplighting .

Target Market(s)

21-28 year old females

Contact Information for Business Card

Has to have logo, website, email, and phone number

Font styles to use
Other font styles liked:
• open to font choice, modern, clean
Designer to choose
33a6d7
0791cd
0555a3
ffffff

Requirements
Must have
• Has to have logo, website, email, and phone number
Nice to have
• I really like the design of the new torvane credit card. I also included my logo and some designs I like
Should not have
• clutter or too much info

```html
<!DOCTYPE html>
<html lang="en">
<head>
<meta charset="utf-8">
<title>Tidewell Event Group – Business Card</title>
<link href="https://fonts.googleapis.com/css2?family=Open+Sans:wght@400;600;700&display=swap" rel="stylesheet">
<style>
  :root {
    --backdrop: #2e2e30;
    --card: #1b1b1d;
    --silver: #a9abaf;
    --white: #ffffff;
    --blue-light: #33a6d7;
    --blue: #0791cd;
    --blue-deep: #0555a3;
    --ring-dark: #3a3b3e;
    --ring-light: #8d8f93;
  }
  * { box-sizing: border-box; margin: 0; padding: 0; }
  html, body { width: 799px; height: 1200px; overflow: hidden; }
  body {
    background: var(--backdrop);
    font-family: "Open Sans", Arial, sans-serif;
    position: relative;
  }
  .card {
    position: absolute;
    left: 90px;
    width: 620px;
    height: 354px;
    background: var(--card);
    border-radius: 4px;
    box-shadow: 0 12px 30px rgba(0,0,0,.45);
    overflow: hidden;
  }
  .card--front { top: 150px; }
  .card--back { top: 700px; }

  /* Front */
  .front-wordmark {
    position: absolute;
    inset: 0;
    display: flex;
    flex-direction: column;
    align-items: center;
    justify-content: center;
    color: var(--silver);
    font-weight: 600;
  }
  .front-wordmark__name { font-size: 50px; letter-spacing: 4px; line-height: 1; }
  .front-wordmark__sub { font-size: 15px; letter-spacing: 9px; margin-top: 10px; }

  /* Back */
  .back-info {
    position: absolute;
    left: 40px;
    top: 42px;
  }
  .back-wordmark { color: var(--white); font-weight: 600; line-height: 1; }
  .back-wordmark__name { font-size: 27px; letter-spacing: 2px; }
  .back-wordmark__sub { font-size: 9px; letter-spacing: 5px; margin-top: 4px; }
  .person { margin-top: 20px; }
  .person__name { color: var(--blue); font-size: 21px; font-weight: 700; }
  .person__role { color: var(--white); font-size: 13px; margin-top: 2px; }
  .contacts { list-style: none; margin-top: 18px; }
  .contacts li {
    display: flex; align-items: center; gap: 10px;
    color: var(--white); font-size: 13px; margin-bottom: 8px;
  }
  .contacts svg { width: 13px; height: 13px; flex: none; }

  .emblem {
    position: absolute;
    right: 40px;
    top: 47px;
    width: 260px;
    height: 260px;
    border-radius: 50%;
    background: radial-gradient(circle, var(--ring-dark) 58%, var(--ring-light) 70%, var(--ring-dark) 84%, transparent 86%);
  }
  .emblem__core {
    position: absolute;
    inset: 42px;
    border-radius: 50%;
    background: var(--card);
    border: 2px solid var(--silver);
    display: flex; align-items: center; justify-content: center;
    color: var(--blue);
    font-size: 28px;
    font-weight: 600;
    letter-spacing: 1px;
  }
</style>
</head>
<body>
  <section class="card card--front">
    <div class="front-wordmark">
      <span class="front-wordmark__name">TIDEWELL</span>
      <span class="front-wordmark__sub">EVENT GROUP</span>
    </div>
  </section>

  <section class="card card--back">
    <div class="back-info">
      <div class="back-wordmark">
        <div class="back-wordmark__name">TIDEWELL</div>
        <div class="back-wordmark__sub">EVENT GROUP</div>
      </div>
      <div class="person">
        <div class="person__name">Mara Ellison</div>
        <div class="person__role">Founder &amp; CEO</div>
      </div>
      <ul class="contacts">
        <li>
          <svg viewBox="0 0 16 16" aria-hidden="true"><path fill="#0791cd" d="M3 1h3l1.5 4-2 1.3a9 9 0 0 0 4.2 4.2L11 8.5l4 1.5v3a2 2 0 0 1-2 2A13 13 0 0 1 1 3a2 2 0 0 1 2-2z"/></svg>
          555 0148 2260
        </li>
        <li>
          <svg viewBox="0 0 16 16" aria-hidden="true"><rect x="1" y="3" width="14" height="10" rx="1" fill="#0791cd"/><path d="M1.5 3.5 8 9l6.5-5.5" stroke="#1b1b1d" stroke-width="1.4" fill="none"/></svg>
          mara@tidewellevents.com
        </li>
        <li>
          <svg viewBox="0 0 16 16" aria-hidden="true"><circle cx="8" cy="8" r="6.5" fill="none" stroke="#0791cd" stroke-width="1.5"/><ellipse cx="8" cy="8" rx="2.8" ry="6.5" fill="none" stroke="#0791cd" stroke-width="1.2"/><path d="M1.5 8h13" stroke="#0791cd" stroke-width="1.2"/></svg>
          www.tidewellevents.com
        </li>
      </ul>
    </div>

    <div class="emblem" role="img" aria-label="Circular sound-level bar ring surrounding the brand name">
      <div class="emblem__core">Tidewell</div>
    </div>
  </section>
</body>
</html>
```